Campaign Website

I need a website for my judicial campaign. I would like a site that directs from this domain as well as a new domain with my married last name. I need separate pages on the site that address my diversion programs, and a page to allow people to donate with a link to my bank account and a link for people to submit requests to volunteer, get yard signs, etc.

```html
<!DOCTYPE html>
<html lang="en">
<head>
<meta charset="utf-8">
<title>Harper Delaney for Judge</title>
<link href="https://fonts.googleapis.com/css2?family=Lato:wght@400;700;900&family=Roboto:wght@400;500;700&display=swap" rel="stylesheet">
<style>
:root{
  --red:#a8111d;
  --navy:#0a2e5c;
  --ink:#1b1b1b;
  --muted:#555;
  --white:#fff;
  --line:#e3e3e3;
}
*{box-sizing:border-box;margin:0;padding:0}
html,body{width:1200px;height:3575px;overflow:hidden}
body{font-family:'Roboto',sans-serif;color:var(--ink);background:var(--white);position:relative}
.wrap{position:absolute;left:143px;width:912px}
.btn{display:inline-flex;align-items:center;gap:7px;height:50px;padding:0 26px;border-radius:25px;font-family:'Lato',sans-serif;font-weight:900;font-size:16px;text-decoration:none;color:var(--white);background:var(--red);border:2px solid var(--red);white-space:nowrap}
.btn.ghost{background:var(--white);color:var(--red)}
.btn.navy{background:var(--navy);border-color:var(--navy)}
.btn svg{width:15px;height:15px}

/* header */
.site-header{position:absolute;top:0;left:0;width:1200px;height:111px;border-top:3px solid var(--navy);background:var(--white)}
.brand{position:absolute;left:143px;top:34px;font-family:'Lato',sans-serif;font-weight:700;font-size:27px;color:var(--ink)}
.nav{position:absolute;left:428px;top:38px;display:flex;gap:17px;font-family:'Lato',sans-serif;font-weight:700;font-size:14px;white-space:nowrap}
.nav a{color:var(--ink);text-decoration:none;position:relative;padding:8px 0}
.nav a.active{color:var(--red)}
.nav a.active::before{content:"";position:absolute;left:-4px;right:-4px;top:-4px;height:3px;background:var(--red)}
.header-donate{position:absolute;left:940px;top:33px;height:42px;padding:0 23px;font-size:17px;border-radius:21px}

/* hero */
.hero{position:absolute;top:111px;left:0;width:1200px;height:541px}
.hero-photo{position:absolute;inset:0;background:linear-gradient(90deg,#3a2418 0%,#5a3a27 40%,#6b4a34 60%,#4a3225 100%)}
.hero-people{position:absolute;left:700px;top:10px;width:390px;height:531px;border-radius:190px 190px 0 0;background:linear-gradient(180deg,#8a6a55,#d8cfc3 45%,#6b6a48 100%);opacity:.85}
.hero-text{position:absolute;left:143px;top:120px;color:var(--white);font-family:'Lato',sans-serif}
.hero-text .first{font-weight:900;font-size:42px;letter-spacing:1px}
.hero-text .last{font-weight:900;font-size:60px;line-height:1;letter-spacing:1px}
.hero-text p{margin-top:22px;font-weight:700;font-size:20px;line-height:36px;width:480px}
.hero-text .btn{margin-top:28px;font-size:17px}

/* welcome */
.welcome{top:736px;text-align:center}
.welcome h1{font-family:'Lato',sans-serif;font-weight:900;font-size:40px;line-height:56px;letter-spacing:1px}
.welcome p{margin-top:28px;font-size:13px;line-height:26px;color:var(--muted)}
.welcome p + p{margin-top:18px}
.welcome .actions{margin-top:40px;display:flex;justify-content:center;gap:18px}
.welcome .btn{height:51px;padding:0 24px}

/* award */
.award{position:absolute;top:1223px;left:0;width:1200px;height:261px;background:var(--navy)}
.award-badge{position:absolute;left:163px;top:1183px;width:340px;height:340px}
.award-text{position:absolute;left:582px;top:1280px;color:var(--white);font-family:'Lato',sans-serif}
.award-text h2{font-weight:900;font-size:42px;letter-spacing:1px}
.award-text p{margin-top:18px;font-weight:700;font-size:17px;line-height:38px;width:470px}

/* biography */
.bio-bg{position:absolute;top:1484px;left:0;width:1200px;height:1371px;background:linear-gradient(180deg,#f7f7f8,#f1f1f3 50%,#f6f6f7)}
.bio{top:1618px;width:448px}
.bio h2{font-family:'Lato',sans-serif;font-weight:900;font-size:42px;letter-spacing:1px}
.bio p{margin-top:20px;font-size:13px;line-height:23px;color:var(--muted);text-align:justify}
.bio p:first-of-type{margin-top:30px}
.bio .btn{margin-top:36px;height:51px}
.bio-photo{position:absolute;left:630px;top:1570px;width:470px;height:550px}
.divider{position:absolute;left:143px;top:2210px;width:912px;height:1px;background:var(--line)}

/* events */
.events-title{position:absolute;top:2305px;left:0;width:1200px;text-align:center;font-family:'Lato',sans-serif;font-weight:900;font-size:40px;letter-spacing:1px}
.event{position:absolute;top:2407px;width:279px;height:273px;overflow:hidden}
.event .shot{position:absolute;inset:0}
.event svg.band{position:absolute;left:0;bottom:0;width:279px}
.event .name{position:absolute;left:17px;bottom:19px;color:var(--white);font-weight:500;font-size:18px}
.event .go{position:absolute;right:18px;bottom:18px;width:16px;height:16px}
.event.featured .name{bottom:70px;left:18px}
.event.featured .desc{position:absolute;left:18px;bottom:24px;width:210px;color:var(--white);font-size:11.5px;line-height:19px}
.event.featured .go{bottom:26px}
.view-all{position:absolute;left:500px;top:2721px;width:200px;height:45px;border:1.5px solid #ddd;border-radius:23px;background:var(--white);display:flex;align-items:center;justify-content:center;gap:4px;font-family:'Lato',sans-serif;font-weight:900;font-size:14px;color:var(--red)}
.view-all svg{width:12px;height:12px}

/* cta */
.cta{position:absolute;top:2855px;left:0;width:1200px;height:377px;background:linear-gradient(90deg,#9e0f1b,#b0141f 50%,#a3101c);text-align:center;color:var(--white)}
.cta .eyebrow{margin-top:106px;font-size:17px;letter-spacing:1.5px}
.cta h2{margin-top:6px;font-family:'Lato',sans-serif;font-weight:900;font-size:32px;letter-spacing:2.5px}
.cta .sub{margin-top:6px;font-family:'Lato',sans-serif;font-weight:700;font-size:20px;letter-spacing:2px}
.cta .btn{margin-top:38px;height:46px;padding:0 36px;font-weight:700;font-size:18px}

/* footer */
.footer{position:absolute;top:3232px;left:0;width:1200px;height:343px;background:linear-gradient(180deg,#0b3266,#0a2c5a)}
.footer h3{position:absolute;top:82px;color:var(--white);font-weight:500;font-size:18px}
.contact-line{position:absolute;left:145px;display:flex;align-items:center;gap:14px;color:var(--white);font-size:14px}
.contact-line svg{width:15px;height:15px}
.subscribe-field{position:absolute;left:488px;top:114px;width:278px;height:38px;border:1px solid #c9d2df;background:var(--white);display:flex;align-items:center;justify-content:space-between;padding:0 14px;font-size:12px;color:#333}
.subscribe-field svg{width:13px;height:13px}
.subscribe-btn{position:absolute;left:488px;top:166px;width:116px;height:33px;border-radius:17px;background:var(--red);color:var(--white);font-weight:700;font-size:13px;display:flex;align-items:center;justify-content:center}
.socials{position:absolute;left:888px;top:113px;display:flex;gap:8px}
.socials span{width:34px;height:34px;border-radius:50%;display:block}
.footer-rule{position:absolute;left:143px;top:245px;width:912px;height:1px;background:rgba(255,255,255,.45)}
.copyright{position:absolute;top:290px;left:0;width:1200px;text-align:center;color:var(--white);font-size:14px;word-spacing:1px}
.copyright .sep{margin:0 15px}
</style>
</head>
<body>

<header class="site-header">
  <div class="brand">Harper Delaney</div>
  <nav class="nav">
    <a class="active">HOME</a><a>BIOGRAPHY</a><a>EVENTS</a><a>ENDORSEMENTS</a><a>MORE</a><a>CONTACT</a>
  </nav>
  <a class="btn header-donate">DONATE</a>
</header>

<section class="hero">
  <div class="hero-photo" role="img" aria-label="Wooden fence backdrop"></div>
  <div class="hero-people" role="img" aria-label="Photo of the candidate with her husband, smiling outdoors"></div>
  <div class="hero-text">
    <div class="first">HARPER</div>
    <div class="last">DELANEY</div>
    <p>Lorem ipsum dolor sit amet consectetur adipiscing elit sed do eiusmod tempor incididunt.</p>
    <a class="btn">DONATE NOW <svg viewBox="0 0 16 16"><circle cx="8" cy="8" r="8" fill="#fff"/><path d="M4 8h6M8 5l3 3-3 3" stroke="#a8111d" stroke-width="2" fill="none"/></svg></a>
  </div>
</section>

<section class="wrap welcome">
  <h1>WELCOME TO HARPER<br>DELANEY</h1>
  <p>y candidacy is based on the belief that the judiciary needs to be accountable to the citizens it serves. This starts with being present and accessible to ensure that both victims of crime, as well as those accused, have their day in court without unnecessary delays.</p>
  <p>Additionally, it is incumbent upon the judiciary to be proactive and innovative by starting programs that work to deter crime and reduce the recidivism rate. When elected, I will start a first time offenders program to help those accused of lower level felonies get an education, and develop job skills, so they return to our community as productive citizens, not convicted felons.</p>
  <div class="actions">
    <a class="btn">READ MORE <svg viewBox="0 0 16 16"><circle cx="8" cy="8" r="8" fill="#fff"/><path d="M4 8h6M8 5l3 3-3 3" stroke="#a8111d" stroke-width="2" fill="none"/></svg></a>
    <a class="btn ghost">VOTE NOW <svg viewBox="0 0 16 16"><circle cx="8" cy="8" r="8" fill="#a8111d"/><path d="M4 8h6M8 5l3 3-3 3" stroke="#fff" stroke-width="2" fill="none"/></svg></a>
  </div>
</section>

<section class="award"></section>
<svg class="award-badge" viewBox="0 0 340 340" role="img" aria-label="Award badge">
  <circle cx="170" cy="170" r="168" fill="#fff"/>
  <circle cx="170" cy="170" r="160" fill="var(--navy)"/>
  <circle cx="170" cy="170" r="104" fill="#fff"/>
</svg>
<div class="award-text">
  <h2>MY AWARD</h2>
  <p>Lorem ipsum dolor sit amet consectetur adipiscing elit, sed do eiusmod tempor incididunt.</p>
</div>

<div class="bio-bg" role="img" aria-label="Faded photo of campaign supporters"></div>
<section class="wrap bio">
  <h2>BIOGRAPHY</h2>
  <p>I was born in Maple Ridge, Ohio, the middle child of five siblings to Warren and Loretta Harper.</p>
  <p>I matriculated at the Eastbrook State University where I received a Bachelor of Arts in Political Science. I earned my Juris Doctorate from the Westfield School of Law where I served as the President of the Student Law Society.</p>
  <p>I began my prosecutorial career in Cedar County, where I worked as the Chief Juvenile Prosecutor. I currently work in the Gang Unit as a Felony Assistant District Attorney at the Lakeview County District Attorney's Office, handling all crimes involving documented gang members.</p>
  <a class="btn">READ MORE <svg viewBox="0 0 16 16"><circle cx="8" cy="8" r="8" fill="#fff"/><path d="M4 8h6M8 5l3 3-3 3" stroke="#a8111d" stroke-width="2" fill="none"/></svg></a>
</section>
<svg class="bio-photo" viewBox="0 0 470 550" role="img" aria-label="Portrait of the candidate in a blue jacket">
  <defs>
    <linearGradient id="portrait" x1="0" y1="0" x2="0" y2="1">
      <stop offset="0" stop-color="#6b4a3a"/><stop offset=".45" stop-color="#a0705a"/><stop offset=".6" stop-color="#2a55b8"/><stop offset="1" stop-color="#1f3f8f"/>
    </linearGradient>
  </defs>
  <circle cx="285" cy="295" r="208" fill="var(--red)"/>
  <circle cx="262" cy="300" r="203" fill="#fff"/>
  <circle cx="240" cy="300" r="203" fill="#fff"/>
  <circle cx="250" cy="300" r="195" fill="#d9d9d9"/>
  <circle cx="225" cy="300" r="197" fill="url(#portrait)"/>
</svg>
<div class="divider"></div>

<h2 class="events-title">MY ENEVTS</h2>
<article class="event" style="left:144px">
  <div class="shot" role="img" aria-label="Group photo of volunteers in a hallway" style="background:linear-gradient(160deg,#c9bfb3,#6d5a52 50%,#2f2a2a)"></div>
  <svg class="band" viewBox="0 0 279 80" preserveAspectRatio="none"><polygon points="0,25 279,0 279,80 0,80" fill="var(--navy)"/></svg>
  <div class="name">EVENT NAME</div>
  <svg class="go" viewBox="0 0 16 16"><circle cx="8" cy="8" r="8" fill="#fff"/><path d="M8 12V5M5 8l3-3 3 3" stroke="#0a2e5c" stroke-width="2" fill="none"/></svg>
</article>
<article class="event featured" style="left:460px">
  <div class="shot" role="img" aria-label="Group photo at a community meeting" style="background:linear-gradient(180deg,#c8c9cc,#7c7f88 45%,#2e3444)"></div>
  <svg class="band" viewBox="0 0 279 135" preserveAspectRatio="none"><polygon points="0,0 279,55 279,135 0,135" fill="var(--red)"/></svg>
  <div class="name">EVENT NAME</div>
  <div class="desc">Lorem ipsum dolor sit amet consectetur adipiscing tempor incididunt...</div>
  <svg class="go" viewBox="0 0 16 16"><circle cx="8" cy="8" r="8" fill="#fff"/><path d="M4 8h6M8 5l3 3-3 3" stroke="#a8111d" stroke-width="2" fill="none"/></svg>
</article>
<article class="event" style="left:777px">
  <div class="shot" role="img" aria-label="Photo of a youth discussion circle" style="background:linear-gradient(160deg,#b8ab90,#6b5d4c 50%,#3a3138)"></div>
  <svg class="band" viewBox="0 0 279 80" preserveAspectRatio="none"><polygon points="0,0 279,25 279,80 0,80" fill="var(--navy)"/></svg>
  <div class="name">EVENT NAME</div>
  <svg class="go" viewBox="0 0 16 16"><circle cx="8" cy="8" r="8" fill="#fff"/><path d="M8 12V5M5 8l3-3 3 3" stroke="#0a2e5c" stroke-width="2" fill="none"/></svg>
</article>
<a class="view-all">VIEW ALL EVENTS <svg viewBox="0 0 16 16"><circle cx="8" cy="8" r="8" fill="#a8111d"/><path d="M4 8h6M8 5l3 3-3 3" stroke="#fff" stroke-width="2" fill="none"/></svg></a>

<section class="cta" role="img" aria-label="Red-tinted photo of supporters">
  <div class="eyebrow">ALWAYS LIVE WITH WORLD</div>
  <h2>DON’T FORGET THIS VOTE ME,</h2>
  <div class="sub">ADD TO YOUR CALENDAR NOW!</div>
  <a class="btn navy">VOTE ME <svg viewBox="0 0 16 16"><circle cx="8" cy="8" r="8" fill="#fff"/><path d="M4 8h6M8 5l3 3-3 3" stroke="#0a2e5c" stroke-width="2" fill="none"/></svg></a>
</section>

<footer class="footer">
  <h3 style="left:145px">CONTACT US</h3>
  <div class="contact-line" style="top:128px"><svg viewBox="0 0 16 16"><path d="M3 1l3 3-2 2c1 2 3 4 5 5l2-2 3 3-2 3C7 15 1 9 1 3z" fill="#fff"/></svg>(+1) 555 014 2290</div>
  <div class="contact-line" style="top:170px"><svg viewBox="0 0 16 16"><rect x="1" y="3" width="14" height="10" fill="#fff"/><path d="M1 3l7 6 7-6" stroke="#0a2e5c" stroke-width="1.5" fill="none"/></svg>info@harperdelaney.org</div>
  <h3 style="left:488px">NEWSLETTER SUBSCRIBE</h3>
  <div class="subscribe-field">Enter Email <svg viewBox="0 0 16 16"><rect x="1" y="3" width="14" height="10" fill="#333"/><path d="M1 3l7 6 7-6" stroke="#fff" stroke-width="1.5" fill="none"/></svg></div>
  <div class="subscribe-btn">SUBSCRIBE</div>
  <h3 style="left:888px">FOLLOW US ON</h3>
  <div class="socials" aria-label="Social links">
    <span style="background:#3d5f9c"></span><span style="background:#3ba0dc"></span><span style="background:#d23b2e"></span><span style="background:#a63fc2"></span>
  </div>
  <div class="footer-rule"></div>
  <div class="copyright">Copyrights © 2019 Harper Delaney. All Rights Reserved<span class="sep">|</span>Privacy Policy<span class="sep">|</span>Terms Of Services.</div>
</footer>

</body>
</html>
```